Lantern Hollow Brewing Company New Website with Food Ordering

We need a wordpress-based website for a local brewery & pizza kitchen. The final design will have 6 primary pages: home page, order pizza, our beers, visit us, about us, merch store. The website must integrate with tillpoint for kitchens for online ordering for takeout and delivery. It will also a feature a selection of beers and help customers navigate to the brewery and find hours of operation. The existing website is lanternhollowbrew.example. This is a very old website.

Industry/Entity Type

Brewery and food service

Coding

Coded - Design and coding required

Number of Pages Required

5+ page

Font styles to use
Sans Serif

Requirements
Must have
• ability to integrate seamlessly with tillpoint for kitchens, 21+ age gate
Nice to have
• see attached pdf

```html
<!DOCTYPE html>
<html lang="en">
<head>
<meta charset="utf-8">
<title>Lantern Hollow Brewing Company</title>
<link rel="stylesheet" href="https://fonts.googleapis.com/css2?family=Montserrat:wght@500;700;800&family=Mulish:wght@400;600&display=swap">
<style>
:root{
  --red:#c8102e;
  --ink:#111;
  --paper:#f7f6f5;
  --grey:#f3f2f2;
  --white:#fff;
  --black:#000;
  --can-orange:#ec7a2e;
  --can-pink:#e8739f;
  --can-green:#6db43a;
  --can-yellow:#f3dc45;
}
*{margin:0;padding:0;box-sizing:border-box}
html,body{width:1200px;height:2289px;overflow:hidden}
body{position:relative;background:var(--paper);font-family:'Mulish',sans-serif;color:var(--ink)}
.abs{position:absolute}

/* hero */
.hero{position:absolute;left:0;top:0;width:1200px;height:700px;
  background:linear-gradient(180deg,#3a1a17 0%,#6b211c 35%,#5a2a22 65%,#2d2320 100%)}
.hero-shade{position:absolute;inset:0;background:rgba(0,0,0,.28)}
.brand{position:absolute;left:129px;top:32px;display:flex;align-items:center;gap:10px;
  font-family:'Montserrat',sans-serif;font-weight:800;font-size:22px;color:var(--white);line-height:1.1;width:200px}
.brand-square{width:22px;height:22px;background:var(--red);flex:none}
.nav{position:absolute;top:30px;right:134px;display:flex;gap:37px;font-family:'Montserrat',sans-serif;font-weight:500;font-size:15px;color:var(--white)}
.badge{position:absolute;left:932px;top:124px;width:112px;height:112px;border-radius:50%;background:var(--red);
  color:var(--white);font-family:'Montserrat',sans-serif;font-weight:800;font-size:18px;line-height:1.3;
  display:flex;align-items:center;justify-content:center;text-align:center}
.hero-title{position:absolute;left:0;width:1200px;top:254px;text-align:center;color:var(--white);
  font-family:'Montserrat',sans-serif;font-weight:800;font-size:44px;line-height:54px;text-transform:uppercase}
.hero-btn{position:absolute;top:415px;width:171px;height:60px;border:2px solid var(--white);color:var(--white);
  font-family:'Montserrat',sans-serif;font-weight:800;font-size:14px;display:flex;align-items:center;justify-content:center;gap:10px}
.hero-btn.active{background:var(--red);border-color:var(--red)}
.hero-btn svg{width:22px;height:22px;fill:none;stroke:var(--white);stroke-width:1.6}

/* pizza intro */
.pizza-photo{position:absolute;left:155px;top:773px;width:396px;height:510px;
  background:radial-gradient(circle at 45% 45%,#d9a25a 0%,#a5381f 55%,#6d2414 100%)}
.section-heading{font-family:'Montserrat',sans-serif;font-weight:800;font-size:23px;text-transform:uppercase}
.section-heading em{font-style:normal;color:var(--red)}
.rule{width:74px;height:3px;background:var(--red)}
.intro-heading{position:absolute;left:630px;top:780px}
.intro-rule{position:absolute;left:631px;top:820px}
.intro-copy{position:absolute;left:630px;top:856px;width:436px;font-size:14px;line-height:24px;text-align:justify;color:#333}
.solid-btn{position:absolute;left:634px;width:170px;height:46px;background:var(--red);color:var(--white);
  font-family:'Montserrat',sans-serif;font-weight:800;font-size:14px;display:flex;align-items:center;justify-content:center}

/* beers */
.beers{position:absolute;left:0;top:1319px;width:1200px;height:600px;background:var(--grey)}
.beers-heading{position:absolute;left:0;width:1200px;top:1358px;text-align:center}
.beers-rule{position:absolute;left:583px;top:1402px;width:34px}
.beer-card{position:absolute;top:1452px;width:225px;height:401px;background:var(--white)}
.beer-can{position:absolute;left:66px;top:48px;width:93px;height:218px;border-radius:10px 10px 14px 14px;background:var(--tone)}
.beer-can.wide{left:49px;width:116px;top:52px;height:212px}
.beer-name{position:absolute;left:0;width:225px;top:302px;text-align:center;font-family:'Montserrat',sans-serif;font-weight:800;font-size:14px;line-height:17px;text-transform:uppercase}
.beer-name.two{top:288px}
.outline-btn{position:absolute;left:61px;top:343px;width:103px;height:31px;border:1.5px solid var(--red);color:var(--red);
  font-family:'Montserrat',sans-serif;font-weight:700;font-size:11.5px;display:flex;align-items:center;justify-content:center}

/* footer */
.footer{position:absolute;left:0;top:1890px;width:1200px;height:399px;background:var(--black);color:var(--white)}
.footer-brand{position:absolute;left:138px;top:2060px;width:150px;display:flex;align-items:center;gap:10px;
  font-family:'Montserrat',sans-serif;font-weight:800;font-size:20px;line-height:1.15;color:var(--white)}
.footer-col{position:absolute;top:2011px;font-size:12.5px;line-height:19.2px;color:var(--white)}
.footer-col h4{font-family:'Montserrat',sans-serif;font-weight:800;font-size:13px;margin-bottom:11px}
.social{display:flex;gap:14px}
.social span{width:27px;height:27px;border-radius:4px;background:var(--white)}
.footer-rule{position:absolute;left:129px;top:2209px;width:937px;height:1px;background:#555}
.copyright{position:absolute;left:0;width:1200px;top:2239px;text-align:center;font-size:12.5px;color:var(--white)}
</style>
</head>
<body>

<header class="hero">
  <div class="hero-shade" role="img" aria-label="Photo of a square pizza and glasses of beer on a red picnic table"></div>
  <div class="brand"><span class="brand-square"></span>Lantern Hollow</div>
  <nav class="nav"><span>The Kitchen</span><span>Our Beers</span><span>Visit Us</span><span>About Us</span><span>Merch</span></nav>
  <div class="badge">Try<br>Zippy!</div>
  <h1 class="hero-title">Square pizza and great<br>beer in Portland, Maine</h1>
  <a class="hero-btn" style="left:234px"><svg viewBox="0 0 24 24"><rect x="3" y="3" width="18" height="18" rx="2"/><circle cx="8" cy="8" r="1"/><circle cx="16" cy="8" r="1"/><circle cx="12" cy="12" r="1"/><circle cx="8" cy="16" r="1"/><circle cx="16" cy="16" r="1"/></svg>ORDER PIZZA</a>
  <a class="hero-btn" style="left:421px"><svg viewBox="0 0 24 24"><path d="M12 21s-6-6.5-6-11a6 6 0 0 1 12 0c0 4.5-6 11-6 11z"/><circle cx="12" cy="10" r="2.2"/></svg>VISIT US</a>
  <a class="hero-btn active" style="left:605px"><svg viewBox="0 0 24 24"><rect x="5" y="7" width="10" height="14" rx="1"/><path d="M15 10h2.5a1.5 1.5 0 0 1 1.5 1.5v4a1.5 1.5 0 0 1-1.5 1.5H15M5 7c0-2 2-3 5-3s5 1 5 3M8 11v6M12 11v6"/></svg>OUR BEERS</a>
  <a class="hero-btn" style="left:794px"><svg viewBox="0 0 24 24"><circle cx="12" cy="8" r="4"/><path d="M4 21c0-4.5 3.5-7 8-7s8 2.5 8 7z"/></svg>ABOUT US</a>
</header>

<svg class="abs" style="left:0;top:640px" width="1200" height="90" viewBox="0 0 1200 90" aria-hidden="true">
  <polygon points="0,24 560,70 600,84 640,70 1200,24 1200,90 0,90" fill="#f7f6f5"/>
  <polygon points="0,7 600,45 1200,7 1200,24 640,70 600,84 560,70 0,24" fill="#c8102e"/>
  <circle cx="600" cy="67" r="8" fill="#fff"/>
</svg>

<div class="pizza-photo" role="img" aria-label="Top-down photo of a Detroit-style pepperoni pizza with green onions"></div>
<h2 class="section-heading intro-heading">What is <em>Detroit-style pizza?</em></h2>
<div class="rule intro-rule"></div>
<p class="intro-copy">It is a long established fact that a reader will be distracted by the readable content of a page when looking at its layout. The point of using Lorem Ipsum is that it has a more-or-less normal distribution of letters, as opposed to using 'Content here, content here', making it look like readable English. Many desktop publishing packages and web page editors now use Lorem Ipsum as their default model text, and a search for 'lorem ipsum' will uncover many web sites still in their infancy. Various versions have evolved over the years, sometimes by accident, sometimes on purpose (injected humour and the like).</p>
<a class="solid-btn" style="top:1129px">ORDER ONLINE</a>
<a class="solid-btn" style="top:1198px">VIEW FULL MENU</a>

<section class="beers"></section>
<h2 class="section-heading beers-heading">Our <em>Beers</em></h2>
<div class="rule beers-rule"></div>

<article class="beer-card" style="left:132px">
  <div class="beer-can" role="img" aria-label="Photo of a Daybreak beer can" style="--tone:var(--can-orange)"></div>
  <h3 class="beer-name">Daybreak</h3>
  <a class="outline-btn">LEARN MORE</a>
</article>
<article class="beer-card" style="left:369px">
  <div class="beer-can" role="img" aria-label="Photo of a Papaya Party beer can" style="--tone:var(--can-pink)"></div>
  <h3 class="beer-name">Papaya Party</h3>
  <a class="outline-btn">LEARN MORE</a>
</article>
<article class="beer-card" style="left:606px">
  <div class="beer-can" role="img" aria-label="Photo of a Croquet Pils beer can" style="--tone:var(--can-green)"></div>
  <h3 class="beer-name">Croquet Pils</h3>
  <a class="outline-btn">LEARN MORE</a>
</article>
<article class="beer-card" style="left:844px">
  <div class="beer-can wide" role="img" aria-label="Photo of a Zippy spiked lemonade can" style="--tone:var(--can-yellow)"></div>
  <h3 class="beer-name two">Zippy Original<br>Lemonade</h3>
  <a class="outline-btn">LEARN MORE</a>
</article>

<footer class="footer">
  <svg class="abs" style="left:0;top:0" width="1200" height="90" viewBox="0 0 1200 90" aria-hidden="true">
    <polygon points="0,0 1200,0 1200,6 600,46 0,6" fill="#f3f2f2"/>
    <polygon points="0,6 600,46 1200,6 1200,24 640,70 600,84 560,70 0,24" fill="#c8102e"/>
    <circle cx="593" cy="67" r="8" fill="#fff"/>
  </svg>
</footer>
<div class="footer-brand"><span class="brand-square"></span>Lantern Hollow</div>
<div class="footer-col" style="left:364px">
  <h4>HOURS</h4>
  Sunday 12-6pm<br>Monday 12-6pm<br>Tuesday CLOSED<br>Wednesday 12-7pm (kitchen closed)<br>Thursday 12-8pm<br>Friday 12-8pm<br>Saturday 12-8pm
</div>
<div class="footer-col" style="left:689px">
  <h4>MENU</h4>
  The Kitchen<br>Our Beers<br>Visit Us<br>About Us<br>Merch
</div>
<div class="footer-col" style="left:919px">
  <h4>FOLLOW US</h4>
  <div class="social"><span aria-label="Social profile one"></span><span aria-label="Social profile two"></span><span aria-label="Social profile three"></span></div>
</div>
<div class="footer-rule"></div>
<p class="copyright">© 2022 Lantern Hollow Brewing Company</p>

</body>
</html>
```